Bright Harbor Painters Banner

Create a banner that displays and reinforces Bright Harbor Painters’ brand identity while promoting our interior painting services. The banner will be displayed at indoor venues through the winter. The design should be clean, professional, and visually recognizable to both new and returning customers. See attached design brief & logo source files.

```html
<!DOCTYPE html>
<html lang="en">
<head>
<meta charset="utf-8">
<title>Bright Harbor Painters Banner</title>
<link href="https://fonts.googleapis.com/css2?family=Bebas+Neue&family=Poppins:wght@600;700&display=swap" rel="stylesheet">
<style>
  :root {
    --stage: #b6b7b2;
    --banner-dark: #262626;
    --banner-mid: #34373a;
    --green: #6a9150;
    --white: #ffffff;
    --ink: #1f1f1f;
    --divider: rgba(255,255,255,0.45);
  }
  * { margin: 0; padding: 0; box-sizing: border-box; }
  html, body { width: 1068px; height: 1200px; overflow: hidden; }
  body { background: var(--stage); position: relative; font-family: "Poppins", sans-serif; }

  .banner {
    position: absolute; left: 34px; top: 400px;
    width: 1000px; height: 400px;
    background: var(--banner-dark);
    box-shadow: 0 14px 40px rgba(0,0,0,0.35);
    overflow: hidden;
  }
  .banner-backdrop {
    position: absolute; inset: 0;
    background:
      radial-gradient(ellipse at 55% 45%, rgba(80,84,88,0.45), transparent 70%),
      linear-gradient(180deg, var(--banner-mid) 0%, var(--banner-dark) 100%);
  }

  .headline {
    position: absolute; left: 36px; top: 26px;
    font-family: "Bebas Neue", sans-serif;
    font-size: 142px; line-height: 1; letter-spacing: 1px;
    color: var(--white);
  }

  .service-strip {
    position: absolute; left: 41px; top: 151px;
    width: 663px; height: 42px;
    background: var(--green); border-radius: 12px;
    display: flex; align-items: center; justify-content: center;
    color: var(--white); font-weight: 700; font-size: 26px; letter-spacing: 6px;
  }

  .brand-name {
    position: absolute; left: 736px; top: 58px; width: 222px;
    display: flex; flex-direction: column; align-items: center; gap: 12px;
  }
  .brand-dot { width: 62px; height: 62px; border-radius: 50%; background: var(--green); }
  .brand-text {
    color: var(--white); font-weight: 700; font-size: 25px; line-height: 1.15;
    text-align: center; letter-spacing: 1px;
  }

  .services { position: absolute; left: 0; top: 206px; width: 1000px; height: 92px; }
  .service {
    position: absolute; top: 0; transform: translateX(-50%);
    display: flex; flex-direction: column; align-items: center; gap: 6px;
  }
  .service svg { width: 50px; height: 50px; }
  .service-label { color: var(--white); font-weight: 700; font-size: 25px; line-height: 1; white-space: nowrap; }
  .divider {
    position: absolute; top: 4px; height: 84px;
    border-left: 1.5px dashed var(--divider);
  }

  .cta {
    position: absolute; left: 38px; top: 315px;
    width: 914px; height: 54px;
    background: var(--green); border-radius: 27px;
  }
  .cta-lead {
    position: absolute; left: 22px; top: 0; height: 54px;
    display: flex; align-items: center;
    color: var(--white); font-weight: 700; font-size: 27px; letter-spacing: -0.3px;
  }
  .cta-link {
    position: absolute; right: 0; top: 0; width: 497px; height: 54px;
    background: var(--white); border-radius: 27px;
    display: flex; align-items: center; gap: 16px; padding-left: 18px;
  }
  .cta-link svg { width: 26px; height: 26px; }
  .url { font-weight: 700; font-size: 36px; color: var(--ink); letter-spacing: -0.5px; }
  .url .url-name { color: var(--green); }
</style>
</head>
<body>
  <section class="banner">
    <div class="banner-backdrop" role="img" aria-label="Faint dark photograph of a furnished interior room"></div>

    <h1 class="headline">PAINT SMARTER</h1>
    <div class="service-strip">INTERIOR PAINTING SERVICES</div>

    <div class="brand-name">
      <span class="brand-dot"></span>
      <span class="brand-text">BRIGHT HARBOR<br>PAINTERS</span>
    </div>

    <div class="services">
      <div class="service" style="left:90px">
        <svg viewBox="0 0 50 50" aria-hidden="true">
          <g fill="#6a9150">
            <rect x="8" y="2" width="16" height="8"/><rect x="27" y="2" width="16" height="8"/>
            <rect x="2" y="13" width="14" height="8"/><rect x="19" y="13" width="14" height="8"/><rect x="36" y="13" width="12" height="8"/>
            <rect x="8" y="24" width="16" height="8"/><rect x="27" y="24" width="16" height="8"/>
            <rect x="2" y="35" width="14" height="8"/>
            <rect x="16" y="43" width="16" height="6"/>
          </g>
          <rect x="19" y="35" width="29" height="8" fill="#ffffff"/>
        </svg>
        <span class="service-label">Walls</span>
      </div>
      <span class="divider" style="left:167px"></span>

      <div class="service" style="left:259px">
        <svg viewBox="0 0 50 50" aria-hidden="true">
          <rect x="1" y="3" width="48" height="6" rx="1" fill="#ffffff"/>
          <rect x="23" y="9" width="4" height="16" fill="#6a9150"/>
          <path d="M8 38 Q25 22 42 38 Z" fill="#6a9150"/>
          <circle cx="25" cy="41" r="4" fill="#6a9150"/>
        </svg>
        <span class="service-label">Ceilings</span>
      </div>
      <span class="divider" style="left:350px"></span>

      <div class="service" style="left:419px">
        <svg viewBox="0 0 50 50" aria-hidden="true">
          <circle cx="11" cy="12" r="7" fill="none" stroke="#6a9150" stroke-width="4"/>
          <circle cx="11" cy="38" r="7" fill="none" stroke="#6a9150" stroke-width="4"/>
          <path d="M16 17 L44 40 L38 42 Z" fill="#6a9150"/>
          <path d="M16 33 L30 22 L34 26 Z" fill="#6a9150"/>
          <path d="M34 19 L46 10 L40 22 Z" fill="#ffffff"/>
        </svg>
        <span class="service-label">Trim</span>
      </div>
      <span class="divider" style="left:488px"></span>

      <div class="service" style="left:591px">
        <svg viewBox="0 0 50 50" aria-hidden="true">
          <rect x="3" y="3" width="20" height="16" fill="#6a9150"/>
          <rect x="27" y="3" width="20" height="44" fill="#6a9150"/>
          <rect x="3" y="23" width="20" height="24" fill="#ffffff"/>
          <rect x="9" y="29" width="2.5" height="7" fill="#262626"/>
          <rect x="14" y="29" width="2.5" height="7" fill="#262626"/>
          <rect x="30" y="10" width="2.5" height="7" fill="#262626"/>
        </svg>
        <span class="service-label">Cabinets</span>
      </div>
      <span class="divider" style="left:691px"></span>

      <div class="service" style="left:834px">
        <svg viewBox="0 0 50 50" aria-hidden="true">
          <rect x="4" y="2" width="9" height="46" fill="#6a9150"/>
          <rect x="16" y="2" width="9" height="46" fill="#6a9150"/>
          <rect x="38" y="2" width="9" height="22" fill="#6a9150"/>
          <path d="M25 12 H40 V24 H30 V30 H25 Z" fill="#ffffff"/>
        </svg>
        <span class="service-label">Drywall Repair</span>
      </div>
    </div>

    <div class="cta">
      <span class="cta-lead">Book a Free Estimate at</span>
      <div class="cta-link">
        <svg viewBox="0 0 26 26" aria-hidden="true">
          <g fill="none" stroke="#6a9150" stroke-width="2">
            <circle cx="13" cy="13" r="11"/>
            <ellipse cx="13" cy="13" rx="5" ry="11"/>
            <line x1="2" y1="13" x2="24" y2="13"/>
            <line x1="4" y1="7.5" x2="22" y2="7.5"/>
            <line x1="4" y1="18.5" x2="22" y2="18.5"/>
          </g>
        </svg>
        <span class="url">www.<span class="url-name">bhpainters</span>.com</span>
      </div>
    </div>
  </section>
</body>
</html>
```